Dog grooming business card
This is a business card for m dog grooming business like it say above.
In the priorities box below I will have the text that I want on the card.

Industry/Entity Type

Business

Colors

Designer to choose colors to be used in the design.

Requirements
Must have
• My logo and the insurance stamp must be on the card.

Text it must have :

Professional grooming services
Email: lunabrisk@mailvale.net
Text or call 1 705 318 6052
TWF certified/member
Pet first aid certified
Next appointment ___________________________________
Nice to have
• Greens to match my logo

```html
<!DOCTYPE html>
<html lang="en">
<head>
<meta charset="utf-8">
<title>Mira Softpaw – Business Card</title>
<link rel="stylesheet" href="https://fonts.googleapis.com/css2?family=Tinos:wght@400;700&display=swap">
<style>
  :root {
    --backdrop: #d9d9d9;
    --card: #ffffff;
    --green: #9cc73f;
    --green-light: #b8d86a;
    --ink: #2a2a2a;
    --divider: #dde9c4;
    --badge-edge: #3f7fc4;
  }
  * { margin: 0; padding: 0; box-sizing: border-box; }
  html, body {
    width: 1200px; height: 864px; overflow: hidden;
    background: var(--backdrop);
    font-family: "Tinos", "Times New Roman", serif;
    color: var(--ink);
  }
  .sheet {
    position: relative; width: 1200px; height: 864px;
    display: flex; flex-direction: column; align-items: center; justify-content: center; gap: 48px;
  }
  .card {
    position: relative; width: 560px; height: 320px;
    background: var(--card); overflow: hidden;
    box-shadow: 0 6px 18px rgba(0,0,0,.18);
  }
  .card__swoosh { position: absolute; inset: 0; width: 100%; height: 100%; }
  .brand {
    position: absolute; display: flex; align-items: center; gap: 12px;
    font-weight: 700; color: var(--ink); white-space: nowrap;
  }
  .brand__dot { border-radius: 50%; background: var(--green); flex: none; }

  .card--front .brand { left: 50%; top: 92px; transform: translateX(-50%); font-size: 46px; }
  .card--front .brand__dot { width: 40px; height: 40px; }

  .card--back .brand { left: 26px; top: 78px; font-size: 30px; gap: 8px; }
  .card--back .brand__dot { width: 24px; height: 24px; }
  .appointment {
    position: absolute; left: 30px; top: 196px; font-size: 15px;
    display: flex; align-items: flex-end; gap: 8px;
  }
  .appointment__line { width: 120px; border-bottom: 1px solid var(--ink); height: 1px; margin-bottom: 2px; }
  .card__divider {
    position: absolute; left: 270px; top: 50px; width: 1px; height: 180px;
    background: linear-gradient(to bottom, transparent, var(--divider), transparent);
  }
  .details {
    position: absolute; left: 292px; top: 60px; list-style: none;
    font-size: 19px; line-height: 1.45;
  }
  .details__phone { padding-left: 44px; }
  .insurance-badge {
    position: absolute; right: 20px; bottom: 18px; width: 86px; height: 40px;
    background: #fff; border: 2px solid var(--badge-edge); border-radius: 8px;
  }
</style>
</head>
<body>
<main class="sheet">
  <section class="card card--front" aria-label="Card front">
    <svg class="card__swoosh" viewBox="0 0 560 320" preserveAspectRatio="none" aria-hidden="true">
      <path d="M0 175 C 160 300, 400 300, 560 205 L560 320 L0 320 Z" fill="var(--green)"/>
      <path d="M0 210 C 180 320, 420 320, 560 235 L560 320 L0 320 Z" fill="var(--green-light)" opacity=".6"/>
    </svg>
    <div class="brand"><span class="brand__dot"></span><span class="brand__name">Mira Softpaw</span></div>
  </section>

  <section class="card card--back" aria-label="Card back">
    <svg class="card__swoosh" viewBox="0 0 560 320" preserveAspectRatio="none" aria-hidden="true">
      <path d="M0 190 C 150 290, 400 300, 560 215 L560 320 L0 320 Z" fill="var(--green)"/>
      <path d="M0 225 C 180 320, 420 320, 560 245 L560 320 L0 320 Z" fill="var(--green-light)" opacity=".6"/>
    </svg>
    <div class="brand"><span class="brand__dot"></span><span class="brand__name">Mira Softpaw</span></div>
    <p class="appointment">Next appointment <span class="appointment__line"></span></p>
    <div class="card__divider"></div>
    <ul class="details">
      <li>Professional grooming services</li>
      <li class="details__phone">1 705 318 6052</li>
      <li>lunabrisk@mailvale.net</li>
      <li>TWF certified/member</li>
      <li>Pet first aid certified</li>
    </ul>
    <div class="insurance-badge" role="img" aria-label="Insurance protection badge"></div>
  </section>
</main>
</body>
</html>
```